Sunscreen Package Design Modern SPF 50

Update current package design to a more modern design target women 16-40 Do not make it playful. Vela Mesa is home to movie stars and high income business people PalmSprings is one of the most desired vacation areas in the world. The sun shines 350 days a year. World class Tennis and Golf tournaments are held every year with the worlds top players attending these tournaments

Target Market(s)

Women

Industry/Entity Type

Skin Protection

Font styles to use
Sans Serif

Requirements
Must have
• The words Vela Mesa and KORIVELL

```html
<!DOCTYPE html>
<html lang="en">
<head>
<meta charset="utf-8">
<title>Vela Mesa Korivell Sunscreen and Aftersun</title>
<link rel="stylesheet" href="https://fonts.googleapis.com/css2?family=Montserrat:wght@500;600;700&display=swap">
<style>
  :root {
    --backdrop: #666666;
    --teal: #2aa3b8;
    --teal-deep: #1f8fa3;
    --teal-light: #4cc6d6;
    --silver: #e4e4e6;
    --silver-shade: #c9c9cd;
    --cap: #f4f4f4;
    --white: #ffffff;
    --sun-yellow: #d7d43c;
    --navy: #1f4a6e;
    --brand-teal: #27a9bd;
  }
  * { margin: 0; padding: 0; box-sizing: border-box; }
  html, body { width: 1200px; height: 1029px; overflow: hidden; background: var(--backdrop); }
  .canvas { position: relative; width: 1200px; height: 1029px; }
  .tubes { position: absolute; inset: 0; }
  .label {
    position: absolute; top: 0; width: 400px; height: 1029px;
    text-align: center; font-family: 'Montserrat', sans-serif;
  }
  .label--sunscreen { left: 180px; color: var(--white); }
  .label--aftersun { left: 620px; color: var(--navy); }
  .brand {
    position: absolute; top: 298px; left: 0; width: 100%;
    font-family: 'Montserrat', sans-serif; font-weight: 600; font-size: 54px;
    line-height: 58px; letter-spacing: 4px; text-transform: uppercase;
  }
  .label--aftersun .brand { color: var(--brand-teal); }
  .product {
    position: absolute; top: 438px; left: 0; width: 100%;
    font-weight: 700; font-size: 21px; letter-spacing: 9px; line-height: 30px;
  }
  .label--sunscreen .product { color: var(--sun-yellow); }
  .protection {
    position: absolute; top: 540px; left: 0; width: 100%;
    font-weight: 700; font-size: 17px; line-height: 22px;
  }
  .pill {
    display: inline-block; border: 2px solid var(--white); border-radius: 6px;
    padding: 0 5px; font-size: 14px; line-height: 18px;
  }
  .spf {
    position: absolute; top: 650px; left: 70px; width: 270px; height: 80px;
    display: flex; align-items: center; gap: 18px; text-align: left;
  }
  .spf-figure { font-weight: 600; line-height: 1; }
  .spf-figure small { display: block; font-size: 17px; }
  .spf-figure strong { font-size: 42px; font-weight: 600; }
  .spf-claim { font-weight: 700; font-size: 19px; line-height: 20px; }
  .spf-claim small { display: block; font-size: 7px; font-weight: 600; line-height: 10px; }
  .volume {
    position: absolute; top: 790px; left: 0; width: 100%;
    font-weight: 700; font-size: 14px; letter-spacing: 1px;
  }
  .tagline {
    position: absolute; top: 520px; left: 90px; width: 220px;
    font-weight: 500; font-size: 14px; line-height: 18px; letter-spacing: 1px; color: #4d5660;
  }
  .divider {
    position: absolute; top: 612px; left: 165px; width: 70px; height: 10px;
    background: var(--brand-teal);
  }
  .ingredients {
    position: absolute; top: 640px; left: 0; width: 100%;
    font-weight: 700; font-size: 16px; line-height: 21px; color: var(--brand-teal);
  }
</style>
</head>
<body>
<div class="canvas">
  <svg class="tubes" width="1200" height="1029" viewBox="0 0 1200 1029">
    <defs>
      <linearGradient id="teal-body" x1="0" x2="1">
        <stop offset="0" stop-color="#2295aa"/>
        <stop offset="0.45" stop-color="#2eaabf"/>
        <stop offset="1" stop-color="#1f8ea2"/>
      </linearGradient>
      <linearGradient id="silver-body" x1="0" x2="1">
        <stop offset="0" stop-color="#c8c8cc"/>
        <stop offset="0.45" stop-color="#eeeef0"/>
        <stop offset="1" stop-color="#bdbdc2"/>
      </linearGradient>
      <linearGradient id="swoosh" x1="0" x2="1">
        <stop offset="0" stop-color="#2fb3c6"/>
        <stop offset="0.7" stop-color="#3fd0de"/>
        <stop offset="1" stop-color="#bff1f5"/>
      </linearGradient>
    </defs>

    <g class="tube tube--sunscreen">
      <path d="M180 110 H580 L530 850 H230 Z" fill="url(#teal-body)"/>
      <rect x="180" y="110" width="400" height="22" fill="#2aa0b5"/>
      <path d="M230 520 Q380 660 545 560 Q380 620 230 520 Z" fill="url(#swoosh)"/>
      <rect x="275" y="850" width="210" height="110" rx="14" fill="var(--cap)"/>
      <circle class="brand-dot" cx="380" cy="235" r="40" fill="var(--white)"/>
      <path d="M275 648 A34 34 0 0 1 275 716" fill="none" stroke="var(--white)" stroke-width="3"/>
    </g>

    <g class="tube tube--aftersun">
      <path d="M620 110 H1020 L970 850 H670 Z" fill="url(#silver-body)"/>
      <rect x="620" y="110" width="400" height="22" fill="#dcdce0"/>
      <rect x="715" y="850" width="210" height="110" rx="14" fill="var(--cap)"/>
      <circle class="brand-dot" cx="820" cy="235" r="40" fill="var(--brand-teal)"/>
    </g>
  </svg>

  <section class="label label--sunscreen">
    <h1 class="brand">Vela<br>Mesa</h1>
    <p class="product">KORIVELL®<br>SUNSCREEN</p>
    <p class="protection"><span class="pill">UVA</span> + <span class="pill">UVB</span><br>PROTECTION</p>
    <div class="spf">
      <p class="spf-figure"><small>SPF</small><strong>30</strong></p>
      <p class="spf-claim">BROAD<br>SPECTRUM<small>WATER - RESISTANT (80 MINUTES)</small></p>
    </div>
    <p class="volume">3 FL OZ / 88 mL</p>
  </section>

  <section class="label label--aftersun">
    <h2 class="brand">Vela<br>Mesa</h2>
    <p class="product">KORIVELL®<br>AFTERSUN</p>
    <p class="tagline">HYDRATE YOUR SKIN WITH THESE ESSENTIAL INGREDIENTS</p>
    <div class="divider"></div>
    <p class="ingredients">HYALURONATE<br>ACID CUCUMBER<br>ALOE JOJOBA<br>SUNFLOWER</p>
    <p class="volume">3 FL OZ / 88 mL</p>
  </section>
</div>
</body>
</html>
```